Website for new dental office

I am Dr. Colin Ashford and am building a new dental practice. I specialize in general dentistry. I am young and have a higher end dental practice incorporating very new technologies and would like my website to reflect that. As many dental patients are older, the website must be very easy to navigate. I would like patients to be able to request appointments, and will eventually add on patient information forms (the health history, etc, that you normally fill out in the practice) from my practice management software, so leave an area for that.

Industry/Entity Type

Building

```html
<!DOCTYPE html>
<html lang="en">
<head>
<meta charset="utf-8">
<title>Ashford Dental Clinic</title>
<link href="https://fonts.googleapis.com/css2?family=Open+Sans:ital,wght@0,400;0,600;0,700;1,400;1,600&display=swap" rel="stylesheet">
<style>
:root{
  --teal:#1ca6c6;
  --teal-dark:#1690ad;
  --orange:#f47a1f;
  --ink:#3b3b3b;
  --body:#666;
  --muted:#999;
  --light:#f2f2f2;
  --line:#dcdcdc;
  --footer:#3a3a3a;
  --footer-deep:#2b2b2b;
  --white:#fff;
}
*{box-sizing:border-box;margin:0;padding:0}
html,body{width:1200px;height:2671px;overflow:hidden}
body{font-family:"Open Sans",Arial,sans-serif;color:var(--body);background:var(--white);position:relative}
.abs{position:absolute}
.teal{color:var(--teal)}
.btn-orange{background:var(--orange);color:var(--white);font-weight:600;text-transform:uppercase;font-size:17px;display:flex;align-items:center;justify-content:center;border-radius:3px}
.btn-dark{background:#3d3d3d;color:var(--white);font-weight:600;font-size:14px;display:flex;align-items:center;justify-content:center;border-radius:2px;text-transform:uppercase}
.ph{display:block}

/* top bar */
.topbar{top:0;left:0;width:1200px;height:45px;background:#f4f4f4;font-size:12px;color:#777}
.toplinks{right:262px;top:16px;letter-spacing:.5px}
.toplinks span{margin:0 7px}
.topcall{right:130px;top:13px;font-size:15px;color:#555;display:flex;align-items:center;gap:10px}
.topcall b{color:var(--teal);font-weight:600}

/* header */
.brand{left:118px;top:73px;font-size:31px;color:var(--ink)}
.header-cta{left:829px;top:73px;width:243px;height:45px}

/* nav */
.nav{top:141px;left:0;width:1200px;height:49px;background:linear-gradient(#2bb5d3,var(--teal-dark))}
.nav ul{list-style:none;display:flex;position:absolute;left:120px;top:0;height:49px}
.nav li{color:var(--white);font-size:13.5px;font-weight:600;height:49px;display:flex;align-items:center;padding:0 17.5px;text-transform:uppercase}
.nav li.active{background:#3f3f3f}

/* hero */
.hero{top:190px;left:0;width:1200px;height:462px;overflow:hidden}
.hero-photo{position:absolute;inset:0;background:linear-gradient(90deg,#aeb8bd 0%,#cfd7da 30%,#e7ecee 50%,#f6f7f8 62%,#fafafa 100%)}
.hero-text{right:123px;top:98px;text-align:right}
.hero-text h1{font-weight:400;font-size:40px;line-height:46px;color:var(--teal)}
.hero-text h2{font-weight:400;font-size:46px;line-height:52px;color:var(--ink)}
.hero-text p{font-size:25px;line-height:33px;color:#555;margin-top:6px}
.hero-cta{right:128px;top:292px;width:243px;height:45px}
.dots{display:flex;gap:9px}
.dots i{width:14px;height:14px;border-radius:50%;background:#666;display:block}
.dots i.on{background:var(--teal)}
.hero .dots{left:557px;top:428px}

/* section titles */
.sec-title{font-size:27px;font-weight:400;color:var(--ink);text-align:center}
.rule-title{display:flex;align-items:center;gap:48px;justify-content:center}
.rule-title::before,.rule-title::after{content:"";height:1px;background:var(--line);flex:1}

/* welcome */
.welcome{top:652px;left:0;width:1200px;height:203px}
.welcome .rule-title{position:absolute;left:130px;width:940px;top:27px}
.welcome p{position:absolute;left:130px;width:940px;top:79px;text-align:center;font-size:13.2px;line-height:23px;color:#666}

/* gallery */
.gallery{top:855px;left:0;width:1200px;height:349px;background:var(--light)}
.gallery .rule-title{position:absolute;left:130px;width:940px;top:25px}
.g-card{position:absolute;top:86px;width:300px;height:196px;background:var(--teal)}
.g-img{position:absolute;top:16px;width:128px;height:128px;border:3px solid var(--white)}
.g-img.l{left:16px}.g-img.r{left:156px}
.g-lbl{position:absolute;top:158px;width:128px;text-align:center;color:var(--white);font-weight:600;font-size:15px}
.g-lbl.l{left:16px}.g-lbl.r{left:156px}
.gallery .dots{left:557px;top:312px}

/* services */
.services{top:1204px;left:0;width:1200px;height:324px}
.services h3{position:absolute;left:130px;top:30px;font-size:27px;font-weight:400;color:var(--ink)}
.services .intro{position:absolute;left:130px;top:78px;width:292px;font-size:13.2px;line-height:23px;color:#666}
.arrows{left:130px;top:268px;display:flex;gap:8px}
.arrows span{width:23px;height:23px;border-radius:50%;background:#3d3d3d;display:flex;align-items:center;justify-content:center}
.svc{position:absolute;width:301px;height:120px;border:1px solid #e0e0e0;background:var(--white)}
.svc .ph{position:absolute;left:13px;top:15px;width:86px;height:86px}
.svc h4{position:absolute;left:119px;top:10px;font-size:15px;font-weight:600;color:var(--teal)}
.svc p{position:absolute;left:119px;top:33px;width:170px;font-size:13px;line-height:19px;color:#666}
.svc a{position:absolute;left:119px;top:80px;font-size:12.5px;color:var(--teal);text-decoration:none}

/* about */
.about{top:1528px;left:0;width:1200px;height:379px;background:var(--light)}
.about h3,.testi h3{font-size:27px;font-weight:400;color:var(--ink)}
.about h3{position:absolute;left:130px;top:22px}
.about .photo{position:absolute;left:130px;top:65px;width:217px;height:285px}
.about p{position:absolute;left:366px;top:70px;width:348px;font-size:13.2px;line-height:23px;color:#666}
.about .read{position:absolute;left:371px;top:301px;width:146px;height:42px}
.about .vline{position:absolute;left:749px;top:30px;width:1px;height:320px;background:var(--line)}
.testi h3{position:absolute;left:781px;top:22px}
.quote{position:absolute;left:785px;top:79px;width:286px;height:155px;background:#e9e9e9;border:1px solid #ddd;box-shadow:0 2px 3px rgba(0,0,0,.08)}
.quote::after{content:"";position:absolute;left:90px;bottom:-16px;border:16px solid transparent;border-bottom:0;border-top-color:#e9e9e9}
.quote p{position:absolute;left:18px;top:14px;width:254px;font-size:13px;line-height:23px;font-style:italic;color:#888;text-indent:28px}
.quote .qo{position:absolute;left:16px;top:14px}
.quote .qc{position:absolute;left:182px;top:113px}
.testi .avatar{position:absolute;left:784px;top:270px;width:76px;height:73px}
.testi .who{position:absolute;left:874px;top:308px;font-size:15px;font-style:italic;font-weight:600;color:var(--teal)}
.testi .where{position:absolute;left:874px;top:331px;font-size:13px;font-style:italic;color:#666}

/* news & blog */
.posts{top:1907px;left:0;width:1200px;height:486px}
.posts h3{position:absolute;left:130px;font-size:27px;font-weight:400;color:var(--ink)}
.posts .date{position:absolute;left:132px;top:84px;font-size:15px;font-weight:600;color:#222}
.posts .title{position:absolute;left:132px;top:310px;font-size:15px;font-weight:600;color:#222}
.posts p{position:absolute;left:130px;width:600px;font-size:13.2px;line-height:23px;color:#666}
.posts p a{color:var(--teal);text-decoration:none;font-weight:600}
.posts .readall{position:absolute;left:586px;width:145px;height:43px}
.posts .sep{position:absolute;left:130px;top:253px;width:600px;height:1px;background:var(--line)}
.appt{position:absolute;left:769px;top:46px;width:302px;height:411px;background:var(--teal);border:2px solid #1491ae}
.appt h4{position:absolute;left:18px;top:14px;font-size:24px;font-weight:400;color:var(--white)}
.field{position:absolute;left:20px;width:260px;height:39px;background:var(--white);font-size:14px;color:#999;padding:9px 12px}
.field.msg{height:124px}
.appt .submit{position:absolute;left:170px;top:345px;width:112px;height:42px;border-radius:2px}

/* footer */
.footer{top:2393px;left:0;width:1200px;height:221px;background:var(--footer);color:#ddd}
.footer h5{position:absolute;top:29px;font-size:15px;font-weight:600;color:var(--white);text-transform:uppercase}
.flinks{position:absolute;top:60px;list-style:none;font-size:11.5px;line-height:26px;color:#ccc;text-transform:uppercase}
.social{position:absolute;left:390px;top:58px;list-style:none;font-size:11.5px;line-height:28px;color:#ccc;text-transform:uppercase}
.social li{display:flex;align-items:center;gap:12px}
.social li i{width:15px;height:15px;border-radius:2px;display:block}
.contact{position:absolute;left:557px;top:54px;font-size:11.5px;line-height:19px;color:#ccc}
.contact .name{color:var(--teal);font-size:15px;font-weight:600;line-height:24px}
.contact dl{display:grid;grid-template-columns:72px auto;margin-top:12px;row-gap:2px}
.contact dd{color:var(--white);font-size:13px}
.contact dd.mail{color:var(--teal);font-size:12px}
.map{position:absolute;left:803px;top:30px;width:268px;height:151px;border:2px solid #eee}
.maplink{position:absolute;left:978px;top:190px;font-size:12px;color:var(--teal)}
.copy{top:2614px;left:0;width:1200px;height:57px;background:var(--footer-deep);font-size:11px;color:#aaa;text-align:center;padding-top:21px;text-transform:uppercase}
.copy b{color:var(--teal);font-weight:400}
</style>
</head>
<body>

<div class="abs topbar">
  <div class="abs toplinks">LOGIN<span>|</span>FAQ<span>|</span>SITE MAP</div>
  <div class="abs topcall">
    <svg width="17" height="17" viewBox="0 0 17 17"><rect width="17" height="17" rx="2" fill="#555"/><path d="M5 3.5c.7 0 1.5 1.8 1.5 2.4S5.6 7 5.9 7.8s2 2.5 2.8 2.8 1.3-.8 1.9-.7 2.4.8 2.4 1.5-1 2.1-2 2.1C7.4 13.5 3.5 9.6 3.5 6 3.5 5 4.3 3.5 5 3.5z" fill="#fff"/></svg>
    <span>CALL: <b>+1 800 555 0142</b></span>
  </div>
</div>

<header>
  <div class="abs brand">Ashford <span class="teal">Dental Clinic</span></div>
  <div class="abs btn-orange header-cta">Request Appointment</div>
</header>

<nav class="abs nav">
  <ul>
    <li class="active">Home</li><li>About Us</li><li>Our Services</li><li>Petient Info</li><li>Gallery</li><li>News &amp; Events</li><li>Testimonials</li><li>Blog</li><li>Contact</li>
  </ul>
</nav>

<section class="abs hero">
  <div class="hero-photo" role="img" aria-label="Dentist examining a smiling patient in a modern treatment room"></div>
  <div class="abs hero-text">
    <h1>Welcome to</h1>
    <h2>Ashford Dental Clinic</h2>
    <p>He provides higher end dental practice<br>incorporating very new technologies.</p>
  </div>
  <div class="abs btn-orange hero-cta">Request Appointment</div>
  <div class="abs dots"><i class="on"></i><i></i><i></i><i></i></div>
</section>

<section class="abs welcome">
  <h3 class="sec-title rule-title"><span>Welcome to <span class="teal">Our Dental Clinic</span></span></h3>
  <p>Aliquam molestie, mi et imperdiet euismod, dui purus auctor tellus, et interdum lacus lectus et ante. Sed accumsan sollicitudin sapien, sit amet adipiscing turpis gravida ac. In congue, neque ac lobortis volutpat, libero mauris varius mi, vitae suscipit ipsum ligula vitae risus. Duis aliquam nibh a dui iaculis viverra id a velit. Vivamus egestas risus in magna varius commodo. Sed semper viverra egestas. Etiam pretium porttitor lectus, vel ornare neque porta volutpat.</p>
</section>

<section class="abs gallery">
  <h3 class="sec-title rule-title"><span>Our &nbsp;<span class="teal">Gallery</span></span></h3>
  <div class="g-card" style="left:130px">
    <div class="g-img l ph" role="img" aria-label="Stained teeth before whitening" style="background:linear-gradient(135deg,#c98a86,#d9c08a)"></div>
    <div class="g-img r ph" role="img" aria-label="White teeth after whitening" style="background:linear-gradient(135deg,#c97c80,#f1eee6)"></div>
    <div class="g-lbl l">Before</div><div class="g-lbl r">After</div>
  </div>
  <div class="g-card" style="left:450px">
    <div class="g-img l ph" role="img" aria-label="Damaged teeth before restoration" style="background:linear-gradient(135deg,#a9574c,#c6a27a)"></div>
    <div class="g-img r ph" role="img" aria-label="Restored teeth after treatment" style="background:linear-gradient(135deg,#c56a6a,#f0ece4)"></div>
    <div class="g-lbl l">Before</div><div class="g-lbl r">After</div>
  </div>
  <div class="g-card" style="left:770px">
    <div class="g-img l ph" role="img" aria-label="Teeth with braces before straightening" style="background:linear-gradient(135deg,#e58a9a,#d8d8d8)"></div>
    <div class="g-img r ph" role="img" aria-label="Teeth with braces after straightening" style="background:linear-gradient(135deg,#e98a9c,#e4e4e4)"></div>
    <div class="g-lbl l">Before</div><div class="g-lbl r">After</div>
  </div>
  <div class="abs dots"><i class="on"></i><i></i><i></i><i></i></div>
</section>

<section class="abs services">
  <h3>Our <span class="teal">Services</span></h3>
  <p class="intro">Aliquam molestie, mi et imperdiet euismod, dui purus auctor tellus, et interdum lacus lectus et ante. Sed accumsan sollicitudin sapien, sit amet adipiscing turpis gravida ac. In congue, neque ac lobortis volutpat, libero mauris varius mi, vitae suscipit ipsum ligula vitae risus.</p>
  <div class="abs arrows">
    <span><svg width="9" height="10" viewBox="0 0 9 10"><path d="M6 1L2 5l4 4" stroke="#fff" stroke-width="2" fill="none"/></svg></span>
    <span><svg width="9" height="10" viewBox="0 0 9 10"><path d="M3 1l4 4-4 4" stroke="#fff" stroke-width="2" fill="none"/></svg></span>
  </div>
  <div class="svc" style="left:450px;top:37px">
    <div class="ph" role="img" aria-label="Close-up of clear aligner on teeth" style="background:linear-gradient(135deg,#e9b2a6,#f4e8e2)"></div>
    <h4>Service Heading</h4><p>Sed accumsan et interdum lacus lectus et ante.</p><a>Read More</a>
  </div>
  <div class="svc" style="left:769px;top:37px">
    <div class="ph" role="img" aria-label="Dental mirror checking a patient's teeth" style="background:linear-gradient(135deg,#d38a82,#efe6e2)"></div>
    <h4>Service Heading</h4><p>Sed accumsan et interdum lacus lectus et ante.</p><a>Read More</a>
  </div>
  <div class="svc" style="left:450px;top:176px">
    <div class="ph" role="img" aria-label="Model of a dental implant in the jaw" style="background:linear-gradient(135deg,#d9a0a4,#f3f0ee)"></div>
    <h4>Service Heading</h4><p>Sed accumsan et interdum lacus lectus et ante.</p><a>Read More</a>
  </div>
  <div class="svc" style="left:769px;top:176px">
    <div class="ph" role="img" aria-label="Dentist treating a patient in the chair" style="background:linear-gradient(135deg,#9eb0b8,#ddd6cf)"></div>
    <h4>Service Heading</h4><p>Sed accumsan et interdum lacus lectus et ante.</p><a>Read More</a>
  </div>
</section>

<section class="abs about">
  <h3>About <span class="teal">Dr. Colin Ashford</span></h3>
  <div class="photo ph" role="img" aria-label="Portrait of the dentist in a white coat with a stethoscope" style="background:linear-gradient(180deg,#e4e6e8,#f4f5f6 60%,#ebedef)"></div>
  <p>Aliquam molestie, mi et imperdiet euismod, dui purus auctor tellus, et interdum lacus lectus et ante. Sed accumsan sollicitudin sapien, sit amet adipiscing turpis gravida ac. In congue, neque ac lobortis volutpat, libero mauris varius mi, vitae suscipit ipsum ligula vitae risus. Duis aliquam nibh a dui iaculis viverra id a velit. Vivamus egestas risus in magna varius commodo. Sed semper viverra egestas. Etiam pretium porttitor lectus, vel ornare neque porta volutpat.</p>
  <div class="btn-dark read">Read More</div>
  <div class="vline"></div>
  <div class="testi">
    <h3>Our <span class="teal">Testimonials</span></h3>
    <div class="quote">
      <svg class="qo" width="24" height="18" viewBox="0 0 24 18"><path d="M0 18V9C0 4 3 1 8 0v4C5 5 4 7 4 9h5v9zM13 18V9c0-5 3-8 8-9v4c-3 1-4 3-4 5h5v9z" fill="#1ca6c6"/></svg>
      <p>Duis aliquam nibh a dui iaculis viverra id a velit. Vivamus egestas risus in magna varius commodo. Sed semper viverra egestas. Etiam pretium porttitor lectus, vel ornare neque...</p>
      <svg class="qc" width="24" height="18" viewBox="0 0 24 18"><path d="M24 0v9c0 5-3 8-8 9v-4c3-1 4-3 4-5h-5V0zM11 0v9c0 5-3 8-8 9v-4c3-1 4-3 4-5H2V0z" fill="#1ca6c6"/></svg>
    </div>
    <div class="avatar ph" role="img" aria-label="Photo of the reviewing patient" style="background:linear-gradient(135deg,#9a7a62,#d9bca4)"></div>
    <div class="who">Name goes here</div>
    <div class="where">Location name</div>
  </div>
</section>

<section class="abs posts">
  <h3 style="top:50px">News <span class="teal">&amp; Events</span></h3>
  <div class="date">APRIL 19, 2014</div>
  <p style="top:108px">Aliquam molestie, mi et imperdiet euismod, dui purus auctor tellus, et interdum lacus lectus et ante. Sed accumsan sollicitudin sapien, sit amet adipiscing turpis gravida ac. In congue, neque ac lobortis volutpat, libero mauris varius mi...<a>Read More</a></p>
  <div class="btn-dark readall" style="top:192px">Read All</div>
  <div class="sep"></div>
  <h3 style="top:267px">Blog <span class="teal">Posts</span></h3>
  <div class="title">Aliquam ullamcorper tempor felis, nec condimentum...</div>
  <p style="top:334px">Aliquam molestie, mi et imperdiet euismod, dui purus auctor tellus, et interdum lacus lectus et ante. Sed accumsan sollicitudin sapien, sit amet adipiscing turpis gravida ac. In congue, neque ac lobortis volutpat, libero mauris varius mi...<a>Read More</a></p>
  <div class="btn-dark readall" style="top:418px">Read All</div>

  <form class="appt">
    <h4>Request Appointment</h4>
    <div class="field" style="top:62px">Full Name</div>
    <div class="field" style="top:110px">Email Address</div>
    <div class="field" style="top:157px">Contact No.</div>
    <div class="field msg" style="top:206px">Message</div>
    <div class="btn-orange submit">Submit</div>
  </form>
</section>

<footer class="abs footer">
  <h5 style="left:130px">Quick Links</h5>
  <ul class="flinks" style="left:130px"><li>Home</li><li>About Us</li><li>Our Services</li><li>Petient Info</li><li>Gallery</li></ul>
  <ul class="flinks" style="left:239px"><li>News &amp; Events</li><li>Testimonials</li><li>Blog</li><li>Contact</li></ul>
  <h5 style="left:389px">Connect Us</h5>
  <ul class="social">
    <li><i style="background:#3b5b98"></i>Social Page</li>
    <li><i style="background:#3fa9e0"></i>Microblog</li>
    <li><i style="background:#2c76ad"></i>Network</li>
    <li><i style="background:#c9302c"></i>Video Channel</li>
    <li><i style="background:#f08a24"></i>RSS Feed</li>
  </ul>
  <h5 style="left:557px">Contact Info</h5>
  <div class="contact">
    <div class="name">Ashford Dental Clinic</div>
    <div>1420 ALDER LANE<br>BROOKFIELD, BK2 7QT.</div>
    <dl>
      <dt>PH:</dt><dd>+1 800 555 0142</dd>
      <dt>FAX:</dt><dd>+1 800 555 0143</dd>
      <dt>EMAIL:</dt><dd class="mail">info@ashforddental.example</dd>
    </dl>
  </div>
  <div class="map" role="img" aria-label="Street map showing the clinic location" style="background:linear-gradient(135deg,#e6e2d4,#d7e1c8 50%,#e9e4d8)"></div>
  <div class="maplink">View Large Map</div>
</footer>

<div class="abs copy">Copyright © 2014. <b>Ashford Dental Clinic</b>. All right reserved</div>

</body>
</html>
```